Systems and Technology Consultants - Website

Design & Build a website for a new company which operates in the Systems and Technology space for Transportation, Government and Commercial sectors.

Overall design should be minimalist in nature.
Should also have a feed that provides news and event updates on the main page.
Logo has already been awarded and should be incorporated into the site.

We like the overall layout, functionality and simplicity of the below sites. Submitted designs could be similar to or a combination of the aspects on these sites, or perhaps a whole different concept - we are open to new ideas.
Norvique.com
Teblo.it

Update 1 Dated 27 May 2014

All I am moving away from the Teblo.it website and would like it to be more aligned with Norvique.com not only in layout but in functionality. I will be extending the deadline of this design brief for two weeks to incorporate additional requirements and will add addtional funding to the project.

Apologies for not having more information available to provide but with so many submissions its getting confusing.

Thanks Derek

Please note that the brief has been updated and the deadline has been extended.

Important: We will need two language versions of the website, English and Arabic; the website is hosted on HostPelican

Hello All, Thank you for your submissions. We have narrowed it down to the final 6 designers and I just wanted to take a moment and provide a bit of feedback regarding the concepts that we like and the modifications we are looking for. First, let me mention some of the design functions we like. - At the top of the homepage we really like the "region" or "language" tab so that the website can be viewed in both English and Arabic. - We like the homepage to have clear color variation so that the different sections of the homepage are distinct. Additionally, we like the bottom portion of the homepage to be in red. We feel that draws attention to our contact information. Again, we would like the colors to integrate black, gray-scale, red, etc. - Having a search tab at the top of the home page, or integrated into the main image, so that the site is easy to navigate. - We especially like the main image to have the scrolling tabs at the bottom so it is easy to browse the services offered (Consultancy, Solutions Architecture, Masters Systems Integration, Independent Design Review). - In regards to the services offered tab we really like the idea that a few people presented that have the outside of our logo with an icon in the middle of consultancy, solutions, etc., etc. Secondly, as mentioned in our brief we really enjoy the design of norvique site. Specially, we enjoy the strong iconic images they use, the way the tabs at the top scroll easily, and contact us page that generates an email. Lastly, I've included some photos of the concept we have been working on. What we are trying to demonstrate is how our company offers a range of services that are essentially linked together. We provide individual services that when combined present the full service package. We would like this concept to be integrated into the over concept of our website. Please feel free to ask for clarification of any of the above points or contact us if you have any additional questions. We appreciate all of your hard work and are very excited to see the updated designs. Best, Marta Vennick Quelbrant Senior Program Manager marta.vennick@quelbrant-example.com

Industry/Entity Type

Government

Font styles to use
Serif
Sans Serif

Requirements
Must have
• Must work on/adapt to various/mobile devices (responsive)
Must be simple and straightforward
Colors should be in line/matching with logo
2 language versions: English and Arabic (no Thai)
Services should be the first group/row of items after/below the main image
Note: the website will be hosted by hostpelican
Nice to have
• Submit feedback form
What's New section
The banner at the bottom of the site should not be too large; we would like a narrow one more
It would be nice if the header/top banner (with Home, About, etc. tabs) could stay in place as you scroll down (like Norvique and Chatterloop)
We will likely only use one image with a Company slogan on the Home page rather than a carousel of images to rotate through
Should not have
• This is the existing website: http://www.quelbrant-example.org
We do not like the animation, the way the banner icons/titles bounce
Not simple enough, we don't like the functionality or how pages load so slowly
We do not like the logo centered - it should be at the left
The banner and its tabs should not be towards the right, we would like them to be centered, to go all the way across and to be below the logo

```html
<!DOCTYPE html>
<html lang="en">
<head>
<meta charset="utf-8">
<title>Quelbrant — System Professionals</title>
<link rel="stylesheet" href="https://fonts.googleapis.com/css2?family=Open+Sans:wght@300;400;600;700&display=swap">
<style>
  :root {
    --header-bg: #0e1a21;
    --hero-dark: #0a3a50;
    --hero-mid: #0f5f80;
    --hero-light: #1a8fb8;
    --accent-orange: #f39a1e;
    --accent-orange-dark: #e07f0a;
    --teal: #1c8c7e;
    --text-dark: #2a2a2a;
    --text-body: #555;
    --text-muted: #888;
    --band-light: #f6f6f6;
    --footer-bg: #3b3b3b;
    --footer-base: #2c2c2c;
    --footer-text: #a8a8a8;
    --white: #ffffff;
  }
  * { margin: 0; padding: 0; box-sizing: border-box; }
  html, body { width: 771px; height: 1200px; overflow: hidden; background: var(--white); }
  body { position: relative; font-family: 'Open Sans', Arial, sans-serif; color: var(--text-dark); }

  /* Header */
  .site-header { position: absolute; top: 0; left: 0; width: 771px; height: 65px; background: var(--header-bg); }
  .brand { position: absolute; left: 70px; top: 22px; display: flex; align-items: center; gap: 6px; color: var(--white); font-weight: 700; font-size: 13px; letter-spacing: 1.5px; }
  .brand-square { width: 10px; height: 10px; background: var(--white); }
  .nav-marker { position: absolute; left: 360px; top: 0; width: 45px; height: 3px; background: var(--white); }
  .nav-marker::after { content: ""; position: absolute; left: 18px; top: 3px; border: 4px solid transparent; border-top-color: var(--white); }
  .main-nav { position: absolute; right: 77px; top: 24px; display: flex; list-style: none; font-size: 9px; font-weight: 600; color: var(--white); }
  .main-nav li { padding: 0 8px; border-left: 1px solid #556; line-height: 11px; }
  .main-nav li:first-child { border-left: 0; }

  /* Hero */
  .hero { position: absolute; top: 65px; left: 0; width: 771px; height: 361px; background: linear-gradient(100deg, var(--hero-dark) 0%, var(--hero-mid) 55%, var(--hero-light) 100%); }
  .hero-visual { position: absolute; left: 320px; top: 0; width: 410px; height: 340px; background: radial-gradient(ellipse at 55% 55%, #3fe0ff 0%, #1aa6d6 35%, rgba(10,60,85,0) 72%); }
  .hero-title { position: absolute; left: 82px; top: 105px; font-size: 25px; font-weight: 300; color: var(--white); }
  .hero-title strong { font-weight: 600; }
  .hero-text { position: absolute; left: 85px; top: 145px; width: 225px; font-size: 8.6px; line-height: 13.5px; color: #e4f1f6; }
  .hero-button { position: absolute; left: 79px; top: 228px; width: 138px; height: 26px; border-radius: 13px; background: linear-gradient(var(--accent-orange), var(--accent-orange-dark)); color: var(--white); font-size: 9px; font-weight: 600; display: flex; align-items: center; padding-left: 10px; gap: 12px; }
  .hero-button svg { width: 13px; height: 13px; }

  /* Intro */
  .intro { position: absolute; top: 426px; left: 0; width: 771px; height: 144px; background: var(--band-light); text-align: center; }
  .intro-mark { position: absolute; left: 377px; top: 43px; width: 16px; height: 16px; border: 2px solid var(--text-dark); transform: rotate(45deg); }
  .intro-text { position: absolute; left: 140px; top: 78px; width: 491px; font-size: 13px; font-weight: 300; line-height: 16px; color: #444; }
  .intro-text strong { font-weight: 600; color: var(--text-dark); }

  /* Services */
  .services { position: absolute; top: 570px; left: 0; width: 771px; height: 290px; }
  .service { position: absolute; top: 34px; width: 104px; text-align: center; }
  .service-icon { display: block; margin: 0 auto; width: 56px; height: 62px; }
  .service-title { margin-top: 18px; font-size: 10px; font-weight: 600; color: var(--text-dark); }
  .service-text { margin-top: 15px; font-size: 7.3px; line-height: 9.3px; color: var(--text-body); }
  .read-more { display: inline-block; margin-top: 16px; font-size: 8px; color: var(--teal); text-decoration: underline; }
  .section-rule { position: absolute; top: 858px; left: 10px; width: 730px; height: 1px; background: linear-gradient(90deg, transparent, #ddd 20%, #ddd 80%, transparent); }

  /* Articles & News */
  .section-heading { position: absolute; font-size: 13.5px; font-weight: 400; color: var(--text-dark); }
  .articles-divider { position: absolute; left: 445px; top: 875px; width: 1px; height: 195px; background: #e2e2e2; }
  .article { position: absolute; left: 76px; width: 340px; }
  .article-thumb { position: absolute; left: 0; top: 0; width: 52px; height: 55px; border: 2px solid #eee; }
  .thumb-binder { background: linear-gradient(135deg, #cfdcdc, #7d9a9a); }
  .thumb-writing { background: linear-gradient(135deg, #e8e6e0, #9a968c); }
  .article-body { position: absolute; left: 59px; top: 3px; width: 285px; }
  .article-title { font-size: 9.5px; color: var(--text-dark); }
  .article-text { margin-top: 4px; font-size: 7.6px; line-height: 10px; color: var(--text-muted); }
  .article-body .read-more { margin-top: 9px; }
  .news-item { position: absolute; left: 453px; width: 228px; }
  .news-title { font-size: 9.5px; color: var(--teal); }
  .news-line { margin-top: 3px; font-size: 6.6px; color: var(--text-dark); }
  .news-meta { margin-top: 4px; display: flex; justify-content: space-between; font-size: 6.4px; color: #444; }
  .news-meta span:last-child { color: var(--text-muted); }

  /* Footer */
  .site-footer { position: absolute; top: 1088px; left: 0; width: 771px; height: 85px; background: var(--footer-bg); }
  .footer-notch { position: absolute; left: 377px; top: 0; border: 7px solid transparent; border-top-color: var(--white); }
  .footer-nav { position: absolute; left: 78px; top: 26px; display: flex; list-style: none; font-size: 7px; color: var(--footer-text); }
  .footer-nav li { padding: 0 8px; border-left: 1px solid #666; line-height: 8px; }
  .footer-nav li:first-child { border-left: 0; }
  .footer-rule { position: absolute; top: 41px; height: 1px; background: #505050; }
  .footer-contact { position: absolute; top: 50px; display: flex; align-items: center; gap: 6px; font-size: 7px; color: var(--footer-text); }
  .footer-contact svg { width: 10px; height: 10px; }
  .stay-label { position: absolute; left: 545px; top: 23px; font-size: 6.5px; font-weight: 600; letter-spacing: .3px; color: var(--footer-text); }
  .social { position: absolute; left: 545px; top: 50px; display: flex; gap: 12px; }
  .social span { width: 10px; height: 10px; border-radius: 50%; background: #8a8a8a; }
  .footer-base { position: absolute; top: 1173px; left: 0; width: 771px; height: 27px; background: var(--footer-base); display: flex; align-items: center; padding-left: 82px; font-size: 7px; color: #8e8e8e; }
  .footer-base span { padding: 0 10px; border-left: 1px solid #555; }
  .footer-base span:first-child { padding-left: 0; border-left: 0; }
</style>
</head>
<body>

<header class="site-header">
  <div class="brand"><span class="brand-square"></span>QUELBRANT</div>
  <div class="nav-marker"></div>
  <ul class="main-nav">
    <li>Home</li><li>Business Units</li><li>Services</li><li>About Us</li><li>Locations</li><li>Contact Us</li>
  </ul>
</header>

<section class="hero">
  <div class="hero-visual" role="img" aria-label="Photo of a businessman touching a glowing tablet with floating technology icons"></div>
  <h1 class="hero-title">System <strong>Professionals</strong></h1>
  <p class="hero-text">It is a long established fact that a reader will be distracted by the readable content of a page when looking at its layout. The point of using Lorem Ipsum is that it has a more-or-less normal distribution of letters, as opposed to using</p>
  <div class="hero-button">Learn more about Us
    <svg viewBox="0 0 14 14"><circle cx="7" cy="7" r="7" fill="#fff" opacity=".35"/><path d="M3.5 6h4V3.8L11 7l-3.5 3.2V8h-4z" fill="#fff"/></svg>
  </div>
</section>

<section class="intro">
  <div class="intro-mark"></div>
  <p class="intro-text"><strong>Quelbrant specializes</strong> in delivering quality professional services and technical projects that support larger business goals.</p>
</section>

<section class="services">
  <div class="service" style="left:68px">
    <svg class="service-icon" viewBox="0 0 56 62" role="img" aria-label="Consulting icon"><path d="M28 1 55 31 28 61 1 31z" fill="#fff" stroke="#ccc"/><circle cx="28" cy="31" r="11" fill="#2b2b2b"/><circle cx="31" cy="34" r="5" fill="var(--teal)"/></svg>
    <div class="service-title">Consulting</div>
    <p class="service-text">It is a long established fact that a reader will be distracted by the readable content of a page when looking at its layout. The point of using Lorem Ipsum is that it has a more-or-less normal distribution</p>
    <span class="read-more">Read More</span>
  </div>
  <div class="service" style="left:192px">
    <svg class="service-icon" viewBox="0 0 56 62" role="img" aria-label="Engineering icon"><path d="M28 1 55 31 28 61 1 31z" fill="#fff" stroke="#ccc"/><circle cx="28" cy="26" r="6" fill="var(--teal)"/><rect x="20" y="32" width="16" height="10" rx="4" fill="#2b2b2b"/></svg>
    <div class="service-title">Engineering</div>
    <p class="service-text">It is a long established fact that a reader will be distracted by the readable content of a page when looking at its layout. The point of using Lorem Ipsum is that it has a more-or-less normal distribution</p>
    <span class="read-more">Read More</span>
  </div>
  <div class="service" style="left:325px">
    <svg class="service-icon" viewBox="0 0 56 62" role="img" aria-label="Construction icon"><path d="M28 1 55 31 28 61 1 31z" fill="#fff" stroke="#ccc"/><path d="M18 40 24 22 27 24 22 40z" fill="#2b2b2b"/><rect x="25" y="34" width="14" height="7" rx="2" fill="var(--teal)"/></svg>
    <div class="service-title">Construction</div>
    <p class="service-text">It is a long established fact that a reader will be distracted by the readable content of a page when looking at its layout. The point of using Lorem Ipsum is that it has a more-or-less normal distribution</p>
    <span class="read-more">Read More</span>
  </div>
  <div class="service" style="left:455px">
    <svg class="service-icon" viewBox="0 0 56 62" role="img" aria-label="Operations icon"><path d="M28 1 55 31 28 61 1 31z" fill="#fff" stroke="#ccc"/><circle cx="31" cy="31" r="10" fill="var(--teal)"/><rect x="17" y="24" width="6" height="14" fill="#2b2b2b"/></svg>
    <div class="service-title">Operations</div>
    <p class="service-text">It is a long established fact that a reader will be distracted by the readable content of a page when looking at its layout. The point of using Lorem Ipsum is that it has a more-or-less normal distribution</p>
    <span class="read-more">Read More</span>
  </div>
  <div class="service" style="left:581px">
    <svg class="service-icon" viewBox="0 0 56 62" role="img" aria-label="Maintenance icon"><path d="M28 1 55 31 28 61 1 31z" fill="#fff" stroke="#ccc"/><path d="M19 32a9 7 0 0 1 18 0z" fill="var(--teal)"/><rect x="18" y="34" width="20" height="4" rx="2" fill="#2b2b2b"/></svg>
    <div class="service-title">Maintenance</div>
    <p class="service-text">It is a long established fact that a reader will be distracted by the readable content of a page when looking at its layout. The point of using Lorem Ipsum is that it has a more-or-less normal distribution</p>
    <span class="read-more">Read More</span>
  </div>
</section>

<div class="section-rule"></div>

<h2 class="section-heading" style="left:77px; top:880px">Our Articles</h2>
<div class="articles-divider"></div>

<article class="article" style="top:915px">
  <div class="article-thumb thumb-binder" role="img" aria-label="Photo of a spiral-bound notebook"></div>
  <div class="article-body">
    <h3 class="article-title">It is a long established fact that</h3>
    <p class="article-text">It is a long established fact that a reader will be distracted by the readable content of a page when looking at its layout.</p>
    <span class="read-more">Read More</span>
  </div>
</article>
<article class="article" style="top:1002px">
  <div class="article-thumb thumb-writing" role="img" aria-label="Photo of a hand writing with a pen"></div>
  <div class="article-body">
    <h3 class="article-title">It is a long established fact that</h3>
    <p class="article-text">It is a long established fact that a reader will be distracted by the readable content of a page when looking at its layout.</p>
    <span class="read-more">Read More</span>
  </div>
</article>

<h2 class="section-heading" style="left:453px; top:880px">Our News</h2>

<div class="news-item" style="top:911px">
  <h3 class="news-title">Investing In Real Estate</h3>
  <p class="news-line">New terminal opens at Kestrel Bay Airport</p>
  <p class="news-line">August 15, 2013 Concessionaire in Bulgaria's Velmora..</p>
  <div class="news-meta"><span>Read More...</span><span>› May 25. February 2014</span></div>
</div>
<div class="news-item" style="top:983px">
  <h3 class="news-title">Current Projects</h3>
  <p class="news-line">Concessionaire in Bulgaria's Velmora..</p>
  <p class="news-line">Resort to Expand Ski Runs Bulgaria's Best for a Cheap Trip.</p>
  <div class="news-meta"><span>Read More...</span><span>› May 25. February 2014</span></div>
</div>

<footer class="site-footer">
  <div class="footer-notch"></div>
  <ul class="footer-nav">
    <li>Home</li><li>About Us</li><li>Business Unit</li><li>Services</li><li>Locations</li><li>Contact Us</li>
  </ul>
  <div class="footer-rule" style="left:84px; width:407px"></div>
  <div class="footer-rule" style="left:545px; width:142px"></div>
  <div class="footer-contact" style="left:84px">
    <svg viewBox="0 0 10 10"><path d="M5 1 1 5h1.3v4h2.2V6.5h1V9h2.2V5H9z" fill="#8a8a8a"/></svg>Lorem Ipsum is simply dummy text of the printinge
  </div>
  <div class="footer-contact" style="left:298px">
    <svg viewBox="0 0 10 10"><path d="M2 1h2l1 2.5-1.2 1a6 6 0 0 0 1.7 1.7l1-1.2L9 6v2a1 1 0 0 1-1 1A7 7 0 0 1 1 2a1 1 0 0 1 1-1z" fill="#8a8a8a"/></svg>(123) 456-7890
  </div>
  <div class="footer-contact" style="left:382px">
    <svg viewBox="0 0 10 10"><rect x="1" y="2" width="8" height="6" fill="#8a8a8a"/><path d="M1 2l4 3.2L9 2" stroke="#3b3b3b" fill="none"/></svg>contact@companyname.com
  </div>
  <div class="stay-label">STAY CONNECTED</div>
  <div class="social" aria-label="Social links"><span></span><span></span><span></span><span></span><span></span><span></span></div>
</footer>

<div class="footer-base"><span>Quelbrant © 2014</span><span>Legal Notice</span><span>Terms</span></div>

</body>
</html>
```